Private Investment Firm Needs PowerPoint Presentation Template

Design PowerPoint template, take Pinebrook-submitted rough presentation draft, and drop it into new template. See attached Project Brief file for more detail.
Updates

Some decent designs have been submitted but they seem to lack the understanding of our target markets. I am hopeful that more time and feedback will result in better results.

Target Market(s)

Private company owners and intermediaries.

Font styles to use
Serif

Colors
3176b5

Requirements
Must have
• See attached Project Brief.
Nice to have
Should not have
• No B2C fluff--this is a B2B project.

```html
<!DOCTYPE html>
<html lang="en">
<head>
<meta charset="utf-8">
<title>Pinebrook Impact - By the Numbers</title>
<link rel="stylesheet" href="https://fonts.googleapis.com/css2?family=Figtree:wght@400;600;700&family=Libre+Baskerville&display=swap">
<style>
  :root {
    --brand-blue: #3176b5;
    --bright-blue: #1a6fc4;
    --band-blue: #0b6cc0;
    --photo-dark: #0f3a47;
    --photo-mid: #1d5766;
    --text-gray: #555555;
    --cell-light: #f2f2f2;
    --cell-mid: #d8d8d8;
    --white: #ffffff;
    --ink: #333333;
  }
  html, body { margin: 0; padding: 0; overflow: hidden; }
  body { width: 1200px; height: 676px; background: var(--white); }
  .slide { position: relative; width: 1200px; height: 676px; overflow: hidden; background: var(--white); font-family: "Figtree", sans-serif; }
  .side-bar { position: absolute; left: 0; top: 0; width: 44px; height: 676px; background: var(--bright-blue); }
  .side-url {
    position: absolute; left: 22px; top: 338px;
    transform: translate(-50%, -50%) rotate(-90deg);
    font-family: "Libre Baskerville", serif; font-size: 14px; color: var(--white); white-space: nowrap;
  }
  .edge-bar { position: absolute; right: 0; top: 0; width: 12px; height: 676px; background: var(--bright-blue); }
  .page-number { position: absolute; right: 28px; top: 18px; font-family: "Libre Baskerville", serif; font-size: 16px; color: var(--ink); }
  .slide-title {
    position: absolute; left: 86px; top: 82px; margin: 0;
    font-size: 29px; font-weight: 700; line-height: 32px; color: var(--bright-blue); letter-spacing: 0.3px;
  }
  .lead-statement {
    position: absolute; right: 748px; top: 226px; margin: 0; text-align: right;
    font-size: 42px; font-weight: 600; line-height: 42px; letter-spacing: 0.5px; color: var(--text-gray);
  }
  .lead-statement .accent { color: var(--bright-blue); }
  .photo-panel {
    position: absolute; left: 482px; top: 101px; width: 706px; height: 470px;
    background: linear-gradient(120deg, var(--photo-mid), var(--photo-dark) 50%, var(--photo-mid));
  }
  .impact-band { position: absolute; left: 482px; top: 170px; width: 706px; height: 334px; background: var(--band-blue); }
  .impact-table { position: absolute; left: 570px; top: 249px; border-collapse: separate; border-spacing: 4px 0; margin-left: -4px; }
  .impact-table th {
    background: var(--cell-light); color: var(--bright-blue); font-weight: 700; font-size: 14px;
    line-height: 18px; height: 53px; padding: 0; text-align: left; letter-spacing: 0.3px;
  }
  .impact-table th.category { width: 258px; padding-left: 48px; box-sizing: border-box; }
  .impact-table th.figure { width: 136px; padding-left: 34px; box-sizing: border-box; }
  .impact-table th.figure.last { width: 137px; }
  .impact-table td {
    background: var(--cell-mid); color: var(--text-gray); font-size: 14px; height: 35px; padding: 0;
    border-top: 2px solid transparent; background-clip: padding-box; letter-spacing: 0.3px;
  }
  .impact-table tbody tr:first-child td { border-top-width: 12px; }
  .impact-table td.category { padding-left: 42px; }
  .impact-table td.figure { text-align: center; }
  .brand { position: absolute; left: 68px; top: 612px; display: flex; align-items: center; gap: 10px; }
  .brand-dot { width: 34px; height: 34px; border-radius: 50%; background: var(--bright-blue); }
  .brand-name { font-size: 22px; font-weight: 600; color: var(--bright-blue); letter-spacing: 2px; }
</style>
</head>
<body>
<div class="slide">
  <div class="side-bar"><span class="side-url">www.pinebrookcapital.com</span></div>
  <div class="edge-bar"></div>
  <div class="page-number">14</div>

  <h1 class="slide-title">PINEBROOK IMPACT<br>- BY THE NUMBERS</h1>

  <p class="lead-statement"><span class="accent">During Pine-<br>brook’s average<br>investment term,</span><br>our impact has<br>been noteworthy</p>

  <div class="photo-panel" role="img" aria-label="Photograph of scattered dollar bills in dark teal tones"></div>
  <div class="impact-band"></div>

  <table class="impact-table">
    <thead>
      <tr>
        <th class="category">IMPACT CATEGORY</th>
        <th class="figure">ACTUAL<br>IMPACT</th>
        <th class="figure last">MIN/MAX*<br>REMOVED</th>
      </tr>
    </thead>
    <tbody>
      <tr><td class="category">Average Revenue Growth</td><td class="figure">113%</td><td class="figure">91%</td></tr>
      <tr><td class="category">Average EBITDA Growth</td><td class="figure">75%</td><td class="figure">78%</td></tr>
      <tr><td class="category">Average Employee Growth</td><td class="figure">213%</td><td class="figure">49%</td></tr>
    </tbody>
  </table>

  <div class="brand"><span class="brand-dot"></span><span class="brand-name">PINEBROOK</span></div>
</div>
</body>
</html>
```